Brandwyn Fuel Retro Website Design

Have a logo. Need a website design to go along with the logo design. Full Design Specs are here: https://files.plinverdocs.net/sheet/d/8QmRtZxWv3-41pk527LNB_XY4HaPcOdsuw2K-rb6/view

Target Market(s)

Independent Gas Station Owners

Number of Pages Required

1 page

Font styles to use
Sans Serif

Colors

Designer to choose colors to be used in the design.

```html
<!DOCTYPE html>
<html lang="en">
<head>
<meta charset="utf-8">
<title>Brandwyn Fuel Company</title>
<link href="https://fonts.googleapis.com/css2?family=Poppins:wght@400;600;700&family=Open+Sans:wght@400;600&display=swap" rel="stylesheet">
<style>
:root{
  --red:#e3262c;
  --dark:#1d1d1d;
  --text:#555;
  --band:#f3f3f3;
  --white:#fff;
  --pink:#f4d7d9;
  --footer-text:#eee;
}
*{box-sizing:border-box;margin:0;padding:0}
html,body{width:1200px;height:4950px;overflow:hidden;background:var(--white)}
body{position:relative;font-family:"Open Sans",sans-serif;color:var(--text)}
.abs{position:absolute}
h1,h2,h3,.heading{font-family:"Poppins",sans-serif}
.nowrap{white-space:nowrap}

/* header */
.site-header{left:0;top:0;width:1200px;height:148px;background:var(--white)}
.brand{left:92px;top:40px;display:flex;align-items:center;gap:12px;font-family:"Poppins",sans-serif;font-weight:700;font-size:22px;color:var(--dark)}
.brand-dot{width:38px;height:38px;border-radius:50%;background:var(--red)}
.social{left:750px;top:37px;display:flex;gap:12px}
.social span{width:14px;height:14px;border-radius:50%;background:#8a8a8a}
.search{left:887px;top:29px;width:224px;height:33px;border:1px solid #333;font-size:14px;padding:6px 8px;color:#444}
.search svg{position:absolute;right:8px;top:9px}
.main-nav{right:92px;top:82px;display:flex;gap:22px;font-size:14.5px;color:#333}

/* hero */
.hero{left:0;top:148px;width:1200px;height:654px;background:linear-gradient(180deg,#4a4a4a 0%,#3a3a3a 45%,#2f2f2f 100%)}
.hero-title{left:0;top:338px;width:1200px;text-align:center;color:var(--white);font-size:52px;font-weight:700;letter-spacing:.5px}
.hero-sub{left:300px;top:420px;width:600px;text-align:center;color:var(--white);font-size:18px;line-height:28px}
.quote-btn{left:504px;top:498px;width:161px;height:42px;border:1.5px solid var(--white);color:var(--white);font-size:16px;font-weight:600;display:flex;align-items:center;justify-content:center}
.quote-btn svg{position:absolute;bottom:-10px;left:72px}

/* about */
.section-title{color:var(--red);font-weight:700;font-size:37px}
.about-title{left:90px;top:930px}
.about-text{left:90px;top:1013px;width:510px;font-size:16px;line-height:32.5px;text-align:justify}
.read-btn{left:90px;top:1288px;height:48px;display:flex}
.read-btn .label{width:136px;background:var(--red);color:var(--white);font-size:12px;letter-spacing:1px;display:flex;align-items:center;justify-content:center}
.read-btn .arrow{width:58px;background:#333;display:flex;align-items:center;justify-content:center}
.photo-frame{left:756px;top:929px;width:355px;height:423px;background:#f2f3f7;border:2px solid #e2e3ea;box-shadow:4px 6px 14px rgba(0,0,0,.3)}
.photo-frame .photo{position:absolute;left:24px;top:24px;width:305px;height:313px;background:linear-gradient(180deg,#c9ccd1 0%,#c4c4c4 55%,#7d7f83 100%)}

/* band */
.promo-band{left:0;top:1438px;width:1200px;height:450px;background:var(--band)}
.promo-box{left:179px;top:1552px;width:842px;height:221px;border:1.5px solid #666}
.promo-label{left:302px;top:1529px;width:594px;height:48px;background:var(--red);color:var(--white);font-family:"Poppins",sans-serif;font-weight:600;font-size:20px;display:flex;align-items:center;justify-content:center}
.promo-title{left:0;top:1605px;width:1200px;text-align:center;color:var(--red);font-size:32px;font-weight:700}
.promo-text{left:290px;top:1658px;width:620px;text-align:center;font-size:16px;line-height:26px}
.promo-text b{color:var(--red);white-space:nowrap}
.contact-btn{left:471px;top:1750px;height:48px;display:flex}
.contact-btn .label{width:194px;background:var(--red);color:var(--white);font-size:16px;display:flex;align-items:center;justify-content:center}
.contact-btn .arrow{width:66px;background:#333;display:flex;align-items:center;justify-content:center}

/* services */
.services-title{left:0;top:2020px;width:1200px;text-align:center}
.services-sub{left:170px;top:2093px;width:800px;text-align:center;font-size:16px;line-height:26px}
.service-row{left:0;width:1200px;height:416px}
.service-photo{position:absolute;top:0;width:604px;height:416px}
.service-copy{position:absolute;top:0;width:596px;height:416px;padding:64px 0 0 68px}
.service-copy.left{left:0;padding-left:89px;background:var(--band)}
.service-copy.right{left:604px;background:var(--band)}
.service-copy.plain{background:var(--white)}
.service-copy h3{color:var(--red);font-size:37px;font-weight:700;margin-bottom:22px}
.service-copy p{font-size:14px;line-height:27px;width:440px}

/* testimonial */
.testi-shadow{left:77px;top:4013px;width:400px;height:391px;background:var(--pink)}
.testi-photo{left:112px;top:3987px;width:380px;height:379px;background:linear-gradient(180deg,#e6e6e6 0%,#c7bfb6 60%,#a89a8c 100%)}
.testi-name{left:112px;top:4292px;width:380px;height:83px;background:var(--red);color:var(--white);text-align:center;padding-top:16px}
.testi-name strong{display:block;font-family:"Poppins",sans-serif;font-weight:600;font-size:22px;line-height:28px}
.testi-name span{font-size:14px}
.quote-open{left:112px;top:3940px;font-family:"Poppins",sans-serif;font-weight:700;font-size:140px;line-height:140px;color:var(--red)}
.testi-title{left:538px;top:4018px}
.testi-rule{left:538px;top:4083px;width:542px;height:1px;background:#ddd}
.testi-text{left:542px;top:4120px;width:538px;font-size:16px;line-height:27px;text-align:justify;color:#333}
.dots{left:543px;top:4343px;display:flex;gap:9px}
.dots span{width:13px;height:13px;border-radius:50%;background:#bbb}
.dots span.on{background:var(--red)}
.signature{left:671px;top:4308px;width:235px;height:72px;background:linear-gradient(90deg,rgba(60,60,60,.08),rgba(60,60,60,.18),rgba(60,60,60,.05))}
.quote-close{left:880px;top:4270px;font-family:"Poppins",sans-serif;font-weight:700;font-size:140px;line-height:140px;color:#d8d8d8}

/* footer */
.site-footer{left:0;top:4526px;width:1200px;height:424px;background:var(--dark);color:var(--footer-text)}
.footer-brand{left:112px;top:4735px;display:flex;align-items:center;gap:14px;font-family:"Poppins",sans-serif;font-weight:700;font-size:30px;color:var(--white)}
.footer-brand .dot{width:46px;height:46px;border-radius:50%;background:var(--red)}
.footer-col{color:var(--footer-text)}
.footer-col h4{font-family:"Poppins",sans-serif;font-weight:700;font-size:19px;color:var(--white);margin-bottom:22px}
.footer-col li{list-style:none;font-size:15px;line-height:29px}
.quick-links{left:494px;top:4652px}
.contact-info{left:835px;top:4652px}
.contact-info li{display:flex;align-items:flex-start;gap:14px;line-height:34px}
.contact-info svg{margin-top:9px;flex:none}
.copyright{left:0;top:4912px;width:1200px;text-align:center;font-size:15px;color:var(--footer-text)}
</style>
</head>
<body>

<header class="abs site-header">
  <div class="abs brand"><span class="brand-dot"></span>Brandwyn Fuel</div>
  <div class="abs social"><span></span><span></span><span></span><span></span></div>
  <div class="abs search">Search.....
    <svg width="15" height="15" viewBox="0 0 15 15"><circle cx="6" cy="6" r="4.5" fill="none" stroke="#111" stroke-width="2"/><line x1="9.5" y1="9.5" x2="14" y2="14" stroke="#111" stroke-width="2.2"/></svg>
  </div>
  <nav class="abs main-nav"><span>Home</span><span>Our Company</span><span>Products &amp; Services</span><span>Contact Us</span><span>B's Containers</span><span>Employment Opportunities</span></nav>
</header>

<section class="abs hero" role="img" aria-label="Photo of the fuel station building with pickup trucks parked in front"></section>
<h1 class="abs hero-title">BRANDWYN FUEL COMPANY</h1>
<p class="abs hero-sub">Brandwyn Fuel provides the full-scale service of a petroleum distributor, delivering gasoline, diesel and lube oils to retail</p>
<div class="abs quote-btn">FREE A QUOTE
  <svg width="16" height="10" viewBox="0 0 16 10"><polyline points="2,2 8,8 14,2" fill="none" stroke="#e3262c" stroke-width="3"/></svg>
</div>

<h2 class="abs section-title about-title">ABOUT US</h2>
<p class="abs about-text">Brandwyn Fuel provides the full-scale service of a petroleum distributor, delivering gasoline, diesel and lube oils to retail, commercial and farm accounts. Our own fleet of delivery trucks provides distribution of fuel to several counties within the North Texas area.<br>Along with a knowledgeable and professional staff, Brandwyn Fuel makes customer service and satisfaction priority one.</p>
<div class="abs read-btn"><span class="label">READ MORE</span><span class="arrow"><svg width="10" height="16" viewBox="0 0 10 16"><polyline points="2,2 8,8 2,14" fill="none" stroke="#fff" stroke-width="2"/></svg></span></div>
<div class="abs photo-frame"><div class="photo" role="img" aria-label="Photo of the fuel station storefront seen from the road"></div></div>

<section class="abs promo-band"></section>
<div class="abs promo-box"></div>
<div class="abs promo-label">DISTRIBUTION OF FUEL TO SEVERAL COUNTIES</div>
<h2 class="abs promo-title">BRANDWYN FUEL COMPANY</h2>
<p class="abs promo-text">Along with a knowledgeable and professional staff, Brandwyn Fuel makes customer service and satisfaction priority one. Contact us today at <b>(555) 214-7730</b></p>
<div class="abs contact-btn"><span class="label">CONTACT US</span><span class="arrow"><svg width="10" height="16" viewBox="0 0 10 16"><polyline points="2,2 8,8 2,14" fill="none" stroke="#fff" stroke-width="2"/></svg></span></div>

<h2 class="abs section-title services-title">SERVICES</h2>
<p class="abs services-sub">As Brandwyn Fuel Company continues to grow and diversify, Our committment to Customer Service &amp; Satisfaction will remain "Old School"</p>

<section class="abs service-row" style="top:2188px">
  <div class="service-photo" style="left:0;background:linear-gradient(135deg,#6e6a66,#cfd0d2 55%,#8d8a85)" role="img" aria-label="Photo of a white fuel delivery truck"></div>
  <div class="service-copy right"><h3>FUEL DELIVERY</h3><p>Brandwyn Fuel provides fuel delivery for independent gas stations, convenience stores, construction sites or any other commercial need. If you are looking for gasoline, high sulfer diesel fuel, farm diesel or other bulk fuel delivered to your business, we will take care of you!provides fuel delivery for independent gas stations, convenience stores, construction sites or any other commercial need. If you are looking for gasoline, high sulfer diesel fuel, farm diesel or other bulk fuel delivered to your business, we will take care of you!</p></div>
</section>

<section class="abs service-row" style="top:2604px">
  <div class="service-copy left plain"><h3>OIL</h3><p>Looking for speciality auto, tractor, tractor trailer, aviation or other commercial oils and lubricants Brandwyn Fuel can help! Just call one of our customer oriented staff and we will get what you need quick! We have a complete line of aviation oils and lubricants as well as gear lubricants, greases, oils and more!</p></div>
  <div class="service-photo" style="left:604px;width:596px;background:linear-gradient(90deg,#d9d6d0,#3a3a8a 40%,#e2c81a 70%,#c8386a)" role="img" aria-label="Photo of oil jugs and fuel cans on store shelves"></div>
</section>

<section class="abs service-row" style="top:3020px">
  <div class="service-photo" style="left:0;background:linear-gradient(180deg,#8a8580,#e8e8e8 45%,#7a7468)" role="img" aria-label="Photo of white farm fuel tanks"></div>
  <div class="service-copy right"><h3>FARM FUEL</h3><p>Looking for gasoline, diesel red diesel off road fuel or farm diesel? We can deliver straight to your farm! We can setup your farm tanks, take care of EPA containment and deliver fuel when you need it!</p></div>
</section>

<section class="abs service-row" style="top:3436px">
  <div class="service-copy left plain"><h3>CARGO CONTAINERS</h3><p>Want to purchase or lease a storage container, we have what you need! We can deliver or move storage containers to your home, business, construction site or any you need one!</p></div>
  <div class="service-photo" style="left:604px;width:596px;background:linear-gradient(180deg,#c6c8cc,#8f9398 55%,#6d6a60)" role="img" aria-label="Photo of a grey steel cargo container"></div>
</section>

<div class="abs testi-shadow"></div>
<div class="abs testi-photo" role="img" aria-label="Portrait photo of the customer"></div>
<div class="abs quote-open">“</div>
<div class="abs testi-name"><strong>MARA QUILLON</strong><span>Customer</span></div>
<h2 class="abs section-title testi-title">WHAT MY CLIENT SAYS</h2>
<div class="abs testi-rule"></div>
<p class="abs testi-text">Lorem ipsum dolor sit amet, consectetur adipiscing elit. In molestie rutrum nulla nec tempor. In ornare lectus sed urna placerat, vitae dapibus ipsum lobortis. Sed scelerisque porttitor metus, et bibendum felis ultricies quis. In vitae ex vitae nisi posuere sollicitudin eget eu urna. Morbi bibendum ornare malesuada.</p>
<div class="abs dots"><span></span><span class="on"></span><span></span><span></span><span></span></div>
<div class="abs signature" role="img" aria-label="Handwritten customer signature"></div>
<div class="abs quote-close">”</div>

<footer class="abs site-footer"></footer>
<div class="abs footer-brand"><span class="dot"></span>Brandwyn Fuel</div>
<div class="abs footer-col quick-links"><h4>QUICK LINKS</h4><ul><li>Home</li><li>Our Company</li><li>Products &amp; Services</li><li>Contact Us</li><li>B'S Containers</li><li>Employment Opportunities</li></ul></div>
<div class="abs footer-col contact-info"><h4>CONTACT US</h4><ul>
  <li><svg width="14" height="18" viewBox="0 0 14 18"><path d="M7 1a6 6 0 0 1 6 6c0 4.5-6 10-6 10S1 11.5 1 7a6 6 0 0 1 6-6z" fill="#fff"/><circle cx="7" cy="7" r="2.2" fill="#1d1d1d"/></svg><span>418 Harlow Mill Road,<br>Carvell, TX 75990</span></li>
  <li><svg width="16" height="16" viewBox="0 0 16 16"><path d="M3 1l3 3-2 2a10 10 0 0 0 6 6l2-2 3 3-2 2C7 15 1 9 1 3z" fill="#fff"/></svg><span class="nowrap">(555) 214-7730</span></li>
  <li><svg width="17" height="13" viewBox="0 0 17 13"><rect x="1" y="1" width="15" height="11" fill="none" stroke="#fff" stroke-width="1.5"/><polyline points="1,1 8.5,7 16,1" fill="none" stroke="#fff" stroke-width="1.5"/></svg><span>hello@brandwynfuel.example</span></li>
</ul></div>
<p class="abs copyright">© 2019 Brandwyn Fuel Company. All Rights Reserved.</p>

</body>
</html>
```